Lorvex Tilo medical cannibis cultivation company

tag - Tilo rise
Lorvex Tilo medical cannabis cultivation - logo is selected- can we please see bold examples with our selection. We are mainly dealing with medical companies and professionals. We would like to be stand out in the crowd with our designs. Welcome any and all attempts. Thanks

Target Market(s)

Medical and Professional

Industry/Entity Type

Medical And Science

Font styles to use
Sans Serif

Colors

Designer to choose colors to be used in the design.

Requirements
Must have
• Bright colour and be bold- Love the teal and magenta that is currently on the dark background design.
Nice to have
• shading and the 3D affect- The shadowed appearance.
Should not have
• Anything related to illegal activity or un professional manners

```html
<!DOCTYPE html>
<html lang="en">
<head>
<meta charset="utf-8">
<title>Lorvex Tilo Stationery</title>
<link href="https://fonts.googleapis.com/css2?family=Raleway:wght@300;400&family=Roboto:wght@400;500&display=swap" rel="stylesheet">
<style>
:root{
  --backdrop:#dcdcdc;
  --paper:#f6f6f7;
  --cyan:#0aa9e6;
  --magenta:#9c4b9c;
  --ink:#3f3f44;
  --body:#5a5a60;
  --ring:#8c8c90;
  --flap:#050505;
}
*{margin:0;padding:0;box-sizing:border-box}
html,body{width:1200px;height:877px;overflow:hidden;background:var(--backdrop)}
.canvas{position:relative;width:1200px;height:877px}
.sheet{position:absolute;background:var(--paper);box-shadow:0 1px 4px rgba(0,0,0,.22)}
.letterhead{left:61px;top:66px;width:527px;height:742px}
.envelope-back{left:615px;top:299px;width:530px;height:241px;background:#fff}
.envelope-front{left:615px;top:568px;width:530px;height:240px}
.band{position:absolute;left:0;right:0;height:51px;background:var(--magenta);display:flex}
.band .cyan{position:absolute;left:0;top:0;bottom:0;width:93px;background:var(--cyan)}
.letterhead .band{top:41px}
.envelope-front .band{top:26px}
.mark-circle{position:absolute;width:60px;height:60px;border-radius:50%;background:#fff;border:2px solid var(--ring)}
.brand{position:absolute;font-family:Roboto,sans-serif;font-weight:500;color:var(--cyan);font-size:13px;line-height:1;white-space:nowrap;text-align:center;width:110px}
.brand small{display:block;font-size:6px;letter-spacing:1px;text-transform:uppercase;margin-top:2px}
.contact{position:absolute;top:0;height:51px;font-family:Roboto,sans-serif;font-size:8px;line-height:10.5px;color:#fff;display:flex;flex-direction:column;justify-content:center}
.contact .row{display:flex;align-items:center;gap:4px}
.contact svg{width:7px;height:7px;fill:#fff}
.divider{position:absolute;top:16px;width:1px;height:21px;background:#fff}
.letter{position:absolute;left:46px;top:209px;width:438px;font-family:Raleway,sans-serif;color:var(--body)}
.letter .salutation{font-size:13px;font-weight:300;color:var(--ink);margin-bottom:24px}
.letter p{font-size:7.4px;line-height:11.4px;font-weight:400;margin-bottom:11.4px;text-align:justify}
.letter .closing{margin-top:22px}
.signature{position:absolute;left:42px;top:518px;width:92px;height:38px;background:linear-gradient(90deg,rgba(40,70,150,.18),rgba(40,70,150,.06));border-radius:4px}
.flap{position:absolute;left:-1px;top:0;width:532px;height:75px}
.flap-name{position:absolute;left:0;right:0;top:30px;text-align:center;font-family:Roboto,sans-serif;font-weight:500;font-size:9px;color:var(--cyan)}
</style>
</head>
<body>
<div class="canvas">

  <section class="sheet letterhead">
    <div class="band">
      <div class="cyan"></div>
      <div class="contact" style="left:158px">
        <span>4120 Alder Crest Way</span>
        <span>Fairbrook, Nevada 58210</span>
      </div>
      <div class="divider" style="left:275px"></div>
      <div class="contact" style="left:292px">
        <span class="row"><svg viewBox="0 0 10 10"><path d="M2 0l2 2.5-1 1.2a6 6 0 0 0 3.3 3.3l1.2-1L10 8 8.6 10C4 9.5.5 6 0 1.4z"/></svg>555 204 7816</span>
        <span class="row"><svg viewBox="0 0 10 10"><path d="M2.5 0h5v10h-5zM3.5 1v7h3V1z"/></svg>555 319 4427</span>
      </div>
      <div class="divider" style="left:374px"></div>
      <div class="contact" style="left:393px">
        <span class="row"><svg viewBox="0 0 10 10"><path d="M0 2h10v6H0zM1 3l4 2.6L9 3z" fill-rule="evenodd"/></svg>mara@lorvextilo.com</span>
        <span class="row"><svg viewBox="0 0 10 10"><circle cx="5" cy="5" r="5"/></svg>www.lorvextilo.com</span>
      </div>
    </div>
    <div class="mark-circle" style="left:63px;top:40px"></div>
    <div class="brand" style="left:38px;top:116px">Lorvex Tilo<small>Tilo rise</small></div>

    <div class="letter">
      <div class="salutation">Dear Mr. Halden,</div>
      <p>Lorem ipsum dolor sit amet, consectetur adipiscing elit. Donec orci purus, luctus vitae dignissim eu, iaculis sed purus. Vivamus faucibus, ipsum nec aliquet viverra, leo mauris condimentum ligula, sit amet sagittis enim ligula quis arcu. Nam egestas tortor id nisi porttitor mattis. In tortor ante, ultricies in suscipit a, tempus non massa. Vivamus et auctor mi. Fusce vel massa nulla. Phasellus nec eros mauris, et scelerisque orci.</p>
      <p>Donec malesuada orci vitae nulla accumsan porta a id massa. Quisque accumsan iaculis magna sit amet fringilla. Maecenas consequat, magna eget tincidunt semper, odio nibh rutrum mi, id feugiat ante nisi eu risus. Vestibulum nunc orci, rhoncus a placerat in, ultricies in mi. Cras mattis varius eros, vel fringilla nisi suscipit eget. Quisque scelerisque sagittis nulla at porttitor.</p>
      <p>Sed id augue vitae urna euismod commodo aliquet a quam. Pellentesque arcu velit, cursus et malesuada ut, consequat et diam. Nullam erat sem, rhoncus id ullamcorper vitae, rhoncus et arcu. In ultricies ultricies nulla, ut rutrum nisi iaculis at. Donec eu magna a metus ornare faucibus. Fusce aliquet faucibus ultricies. Morbi semper, est id tincidunt gravida, sem arcu adipiscing lacus, ac bibendum nulla leo eu purus. Quisque nec diam sed risus consectetur accumsan quis quis nibh. Vestibulum id purus lorem.</p>
      <p>It is a long established fact that a reader will be distracted by the readable content of a page when looking at its layout. The point of using Lorem Ipsum is that it has a more-or-less normal distribution of letters, as opposed to using 'Content here, content here', making it look like readable English. Many desktop publishing packages</p>
      <p class="closing">Sincerely,</p>
    </div>
    <div class="signature" role="img" aria-label="Handwritten signature of Mara Quell"></div>
  </section>

  <section class="sheet envelope-back">
    <svg class="flap" viewBox="0 0 532 75" preserveAspectRatio="none" aria-hidden="true">
      <path d="M0 0H532L524 45Q520 75 490 75H42Q12 75 8 45Z" fill="var(--flap)"/>
    </svg>
    <div class="flap-name">Lorvex Tilo</div>
  </section>

  <section class="sheet envelope-front">
    <div class="band">
      <div class="cyan"></div>
      <div class="contact" style="left:155px">
        <span>4120 Alder Crest Way</span>
        <span>Fairbrook, Nevada 58210</span>
      </div>
      <div class="divider" style="left:272px"></div>
      <div class="contact" style="left:290px">
        <span class="row"><svg viewBox="0 0 10 10"><path d="M2 0l2 2.5-1 1.2a6 6 0 0 0 3.3 3.3l1.2-1L10 8 8.6 10C4 9.5.5 6 0 1.4z"/></svg>555 204 7816</span>
        <span class="row"><svg viewBox="0 0 10 10"><path d="M2.5 0h5v10h-5zM3.5 1v7h3V1z"/></svg>555 319 4427</span>
      </div>
      <div class="divider" style="left:371px"></div>
      <div class="contact" style="left:390px">
        <span class="row"><svg viewBox="0 0 10 10"><path d="M0 2h10v6H0zM1 3l4 2.6L9 3z" fill-rule="evenodd"/></svg>mara@lorvextilo.com</span>
        <span class="row"><svg viewBox="0 0 10 10"><circle cx="5" cy="5" r="5"/></svg>www.lorvextilo.com</span>
      </div>
    </div>
    <div class="mark-circle" style="left:64px;top:26px"></div>
    <div class="brand" style="left:39px;top:102px">Lorvex Tilo<small>Tilo rise</small></div>
  </section>

</div>
</body>
</html>
```